Etikett für Rotweinflasche
Liebe farbkosmos Atelier, wir werden uns bei der endgültigen Etikettengestaltung (finale Größe + Rückseite) noch an Euch melden. Bitte sendet uns euren Kontakt an helga.brandt@morvelli.wine
Zielgruppe
Morvelli Italia ist ein exklusives Boutique-Weingut in Sizilien, das hochqualitative Spitzenweine in kleinen Mengen mit modernster Technologie und stets nachhaltig erzeugt. Wir hinterfragen sowohl in der Agronomie im Weingarten als auch in der Önologie im Weinkeller alle herrschenden Traditionen und trachten danach, stets das beste Endprodukt zu kreieren. Der vulkanische, kalkreiche Boden Siziliens sowie trockene, sonnenreiche und niederschlagsarme Vegetationsperioden sind unsere optimale Basis.
Zielgruppe: Internationale Genussmenschen jeglichen Alters, die sich bewusst auch höherpreisige Weine (um die €30+) gönnen , vor allem kunstaffine young professionals mit Qualitäts-& Nachhaltigkeitsanspruch
Aufgabenstellung
Das Etikett ist für Rotwein-Flaschen (Cabernet Sauvignon / Nero D'Avola / Frappato / Syrah / Cerasuolo / Petit Verdot / sowie einen Bourdeaux-Cuveè aus Cabernet Sauvignon und Petit Verdot) .
Die Flasche ist reinschwarz, sehr hochwertig und schwer.
Flaschenform: Bordeauxflasche siehe technisches Datenblatt
Sleeve über dem Korken: schwarz mit weißer Schrift wie bisher
Zu gestalten ist das Etikett der Vorderseite. Zumindest die jeweilige Rotwein-Sorte ist auch textlich darzustellen (zwecks Scannen mit Trubel-App)
Der Kreativität kann freien Lauf gelassen werden! Unterscheidbarkeit vom Markt ist explizit gewollt.
Unsere aktuellen Etiketten und Markenauftritt siehe: https://morvelli.wine/shop/

```html
<!DOCTYPE html>
<html lang="it">
<head>
<meta charset="utf-8">
<title>Nero d'Avola – Etikett</title>
<link rel="stylesheet" href="https://fonts.googleapis.com/css2?family=Cormorant+Garamond:wght@500&display=swap">
<style>
  :root {
    --stage: #3d3e43;
    --label-cream: #e9e4d6;
    --art-pink: #c65c93;
    --art-rose: #e7a3b4;
    --art-black: #141418;
    --art-grey: #5a5a60;
    --type-white: #f4f2ee;
  }
  html, body {
    margin: 0;
    width: 1200px;
    height: 900px;
    overflow: hidden;
    background: var(--stage);
  }
  .canvas {
    position: relative;
    width: 1200px;
    height: 900px;
    display: flex;
    align-items: center;
    justify-content: center;
  }
  .front-label {
    position: relative;
    width: 560px;
    height: 590px;
    background: var(--label-cream);
    overflow: hidden;
    box-shadow: 0 20px 50px rgba(0,0,0,0.35);
  }
  .label-artwork {
    position: absolute;
    inset: 0;
    background:
      radial-gradient(ellipse 45% 40% at 55% 62%, var(--art-black) 0%, rgba(20,20,24,0.85) 55%, rgba(20,20,24,0) 100%),
      radial-gradient(ellipse 35% 30% at 30% 40%, var(--art-grey) 0%, rgba(90,90,96,0) 100%),
      radial-gradient(ellipse 60% 35% at 60% 12%, var(--art-pink) 0%, rgba(198,92,147,0.5) 45%, rgba(198,92,147,0) 100%),
      radial-gradient(ellipse 40% 25% at 85% 20%, var(--art-rose) 0%, rgba(231,163,180,0) 100%),
      linear-gradient(180deg, #d8cfd6 0%, var(--label-cream) 45%, #cfcbc2 100%);
  }
  .variety-name {
    position: absolute;
    top: 70px;
    left: 225px;
    margin: 0;
    writing-mode: vertical-rl;
    font-family: "Cormorant Garamond", "EB Garamond", serif;
    font-weight: 500;
    font-size: 40px;
    letter-spacing: 0.04em;
    color: var(--type-white);
    text-transform: uppercase;
  }
</style>
</head>
<body>
  <main class="canvas">
    <section class="front-label">
      <div class="label-artwork" role="img" aria-label="Gemalte dunkle Traubenbeeren mit roten Stielen vor einem pinken, rauchigen Farbschleier auf cremefarbenem Grund"></div>
      <h1 class="variety-name">Nero d'Avola</h1>
    </section>
  </main>
</body>
</html>
```